Business card for Luxury Portable Restroom Trailer company

We are a Luxury Portable Restroom Trailer Company Called FALCRIDGE HIRES. Based in Orange County California. We provide portable restroom trailers for events, such as, Weddings, Concerts, Charity events, Sporting events, Tournaments, Corporate events, ect. We rent and Sell the Luxury restrooms. Our colors are white, grey, and Orange. As you will see in the logo we uploaded.
There are 2 people in the company so the names and titles will change for the 3 people but card will remain the same. Here is the information for each Person: Dwight Penner CFO 555 318-0476
next Person: Leon Marchetti VP 555 318-0476
Next Person: Owen Marchetti CEO 555 318-0476
Information to include on the card: Luxury Restroom Trailers Rental and Sales. Weddings, Concerts, Charity, Sporting and Corp. Events.

```html
<!DOCTYPE html>
<html lang="en">
<head>
<meta charset="utf-8">
<title>Falcridge Hires – Business Card</title>
<link href="https://fonts.googleapis.com/css2?family=Saira+Condensed:wght@400;600;700&display=swap" rel="stylesheet">
<style>
  :root {
    --orange: #ea6a1f;
    --charcoal: #4b4b4d;
    --ink: #505052;
    --paper: #ffffff;
    --backdrop: #e6e6e8;
  }
  * { box-sizing: border-box; margin: 0; padding: 0; }
  html, body {
    width: 1200px;
    height: 900px;
    overflow: hidden;
    background: var(--backdrop);
    font-family: "Saira Condensed", "Arial Narrow", sans-serif;
  }
  .stage {
    width: 1200px;
    height: 900px;
    display: flex;
    flex-direction: column;
    align-items: center;
    justify-content: center;
    gap: 40px;
  }
  .card {
    width: 640px;
    height: 366px;
    border: 9px solid var(--orange);
    display: flex;
    flex-direction: column;
    align-items: center;
    justify-content: center;
    box-shadow: 0 6px 18px rgba(0,0,0,0.18);
  }
  .card--front { background: var(--charcoal); }
  .card--back { background: var(--paper); }

  .brand-name {
    font-weight: 700;
    font-size: 46px;
    letter-spacing: 3px;
    line-height: 1;
  }
  .card--front .brand-name { color: var(--paper); font-size: 54px; }
  .card--back .brand-name { color: var(--orange); margin-bottom: 22px; }

  .person {
    font-size: 27px;
    line-height: 1.1;
    color: var(--ink);
  }
  .person__name { color: var(--orange); font-weight: 700; text-transform: uppercase; }
  .person__title { font-weight: 400; }

  .phone {
    display: flex;
    align-items: center;
    gap: 8px;
    font-size: 25px;
    color: var(--ink);
    margin-top: 2px;
  }
  .phone svg { width: 12px; height: 20px; }

  .services-heading {
    margin-top: 14px;
    font-size: 25px;
    font-weight: 700;
    color: var(--orange);
    text-transform: uppercase;
  }
  .services {
    font-size: 22px;
    color: var(--ink);
    text-align: center;
    line-height: 1.15;
  }
  .sep { color: var(--orange); padding: 0 3px; }
</style>
</head>
<body>
<main class="stage">
  <section class="card card--front" aria-label="Card front">
    <p class="brand-name">FALCRIDGE HIRES</p>
  </section>

  <section class="card card--back" aria-label="Card back">
    <p class="brand-name">FALCRIDGE HIRES</p>
    <p class="person"><span class="person__name">Dwight Penner</span> <span class="sep">|</span><span class="person__title">CFO</span></p>
    <p class="phone">
      <svg viewBox="0 0 12 20" aria-hidden="true"><rect x="1" y="1" width="10" height="18" rx="2" fill="none" stroke="var(--orange)" stroke-width="1.6"/><line x1="4.5" y1="16" x2="7.5" y2="16" stroke="var(--orange)" stroke-width="1.4"/></svg>
      555 318-0476
    </p>
    <p class="services-heading">Our Services</p>
    <p class="services">Luxury Restroom Trailers Rental and Sales <span class="sep">|</span> Weddings<br>
      Concerts <span class="sep">|</span> Charity <span class="sep">|</span> Sporting and Corp <span class="sep">|</span> Events</p>
  </section>
</main>
</body>
</html>
```